Realty Group Needs Classy, Contemporary Letterhead Design

We need a letterhead design for a new realty company located in NY, USA. We buy investment properties to rehabilitate and or keep in our rental portfolio.

```html
<!DOCTYPE html>
<html lang="en">
<head>
<meta charset="utf-8">
<title>Meridian Realty Group – Letterhead</title>
<link href="https://fonts.googleapis.com/css2?family=Quicksand:wght@500;600;700&family=Source+Sans+3:wght@400&family=Mrs+Saint+Delafield&display=swap" rel="stylesheet">
<style>
  :root {
    --brand-purple: #4f2a84;
    --band-grey: #808080;
    --text-dark: #1f1f1f;
    --text-body: #454545;
    --backdrop: #e3e3e3;
    --paper: #ffffff;
  }
  * { margin: 0; padding: 0; box-sizing: border-box; }
  html, body {
    width: 1200px; height: 1200px; overflow: hidden;
    background: var(--backdrop);
  }
  .letterhead {
    position: absolute; left: 190px; top: 20px;
    width: 820px; height: 1160px;
    background: var(--paper);
    box-shadow: 0 2px 8px rgba(0,0,0,0.18);
    overflow: hidden;
  }
  .brand {
    position: absolute; left: 79px; top: 70px;
    display: flex; align-items: center; gap: 12px;
    font-family: "Quicksand", sans-serif; font-weight: 700;
    font-size: 27px; color: var(--brand-purple); letter-spacing: 0.3px;
  }
  .brand-square { width: 30px; height: 30px; background: var(--brand-purple); }
  .office-address {
    position: absolute; right: 72px; top: 66px;
    text-align: right;
    font-family: "Quicksand", sans-serif; font-weight: 500;
    font-size: 13.5px; line-height: 18px; color: var(--text-dark);
  }
  .corner-tab {
    position: absolute; right: 0; top: 57px;
    width: 31px; height: 73px; background: var(--brand-purple);
  }
  .recipient, .salutation, .letter-body {
    position: absolute; left: 77px;
    font-family: "Source Sans 3", sans-serif; font-size: 15.5px;
    line-height: 22px; color: var(--text-body);
  }
  .recipient { top: 235px; }
  .salutation { top: 390px; }
  .letter-body { top: 434px; width: 666px; text-align: justify; }
  .signature {
    position: absolute; right: 84px; top: 780px;
    font-family: "Mrs Saint Delafield", cursive;
    font-size: 64px; color: #111; line-height: 1;
  }
  .contact-row {
    position: absolute; left: 77px; right: 78px; top: 1116px;
    display: flex; justify-content: space-between; align-items: center;
    font-family: "Quicksand", sans-serif; font-weight: 500;
    font-size: 12px; color: var(--text-dark);
  }
  .contact-items { display: flex; gap: 10px; align-items: center; }
  .contact-item { display: flex; align-items: center; gap: 3px; }
  .contact-item svg { width: 10px; height: 10px; }
  .website strong { color: var(--brand-purple); font-weight: 700; }
  .footer-band {
    position: absolute; left: 0; right: 0; top: 1140px; height: 20px;
    background: var(--band-grey);
  }
  .footer-accent {
    position: absolute; left: 77px; top: 1140px;
    width: 360px; height: 20px; background: var(--brand-purple);
  }
</style>
</head>
<body>
  <main class="letterhead">
    <div class="brand"><span class="brand-square"></span>Meridian Realty Group, LLC</div>

    <address class="office-address" style="font-style:normal">
      218 Harbor View Ave,<br>
      Suite 12 Albany<br>
      NY 12207
    </address>
    <div class="corner-tab"></div>

    <p class="recipient">
      Mr. John Doe<br>
      President<br>
      Strategy Accountants<br>
      111 Street Name,<br>
      City State, 12345
    </p>

    <p class="salutation">Dear</p>

    <div class="letter-body">
      <p>Lorem ipsum dolor sit amet, consectetur adipiscing elit. Aenean ut ipsum eget massa hendrerit vestibulum vel in velit. Donec pretium neque velit.</p>
      <p>Aliquam porta lectus nec mauris ornare venenatis. Vivamus non est turpis, et cursus sem. Mauris vehicula erat in diam auctor at bibendum nisl lacinia.</p>
      <p>Morbi imperdiet neque vehicula nunc convallis gravida. Vestibulum iaculis pretium placerat. Integer consequat, est sit amet facilisis eleifend, nibh nibh varius orci, eget dapibus arcu dui non purus. Pellentesque in magna mauris. Duis enim sapien, dictum vitae condimentum a, pulvinar vel lacus. Mauris et molestie nibh. Vestibulum vitae nulla at metus elementum porta sit amet interdum elit. Nulla sollicitudin neque eu nulla volutpat congue.</p>
      <p>Etiam pellentesque, velit id dapibus fermentum, turpis sapien ornare dui, ac tincidunt ligula odio congue purus. Nunc sed ante dui, in porta lectus. Cras nec sem lorem. In hac habitasse platea dictumst. Maecenas id diam quis dui porta tristique. Sed id egestas felis. Donec ullamcorper mattis posuere. Phasellus fermentum eleifend tortor vel dapibus. Vestibulum ante ipsum.</p>
    </div>

    <div class="signature">Jonathan Doe</div>

    <footer class="contact-row">
      <div class="contact-items">
        <span class="contact-item">
          <svg viewBox="0 0 10 10"><path d="M2 1 L3.5 1 L4.2 3 L3.2 3.8 Q4.2 5.8 6.2 6.8 L7 5.8 L9 6.5 L9 8 Q9 9 8 9 Q1 8.5 1 2 Q1 1 2 1 Z" fill="#4f2a84"/></svg>
          555.010.2400
        </span>
        <span class="contact-item">
          <svg viewBox="0 0 10 10"><rect x="2.5" y="0.5" width="5" height="9" rx="0.8" fill="none" stroke="#1f1f1f" stroke-width="0.9"/></svg>
          555.014.7731
        </span>
        <span class="contact-item">
          <svg viewBox="0 0 10 10"><rect x="0.5" y="2" width="9" height="6.5" fill="#4f2a84"/><path d="M0.5 2 L5 5.5 L9.5 2" fill="none" stroke="#fff" stroke-width="0.8"/></svg>
          jonathan@meridianrealty.com
        </span>
      </div>
      <span class="website">www.<strong>meridianrealty</strong>.com</span>
    </footer>
    <div class="footer-band"></div>
    <div class="footer-accent"></div>
  </main>
</body>
</html>
```